Talvique Hotels Business Card and Logo

We need a business card design for a hotel group. I saw a hotel card you designed and really liked it. We have multiple properties with different brands. Were hoping that the card would be unique and find a way to list out all our properties. Our web address is www.talviquehotels.com. I have attached some photos of card designs I like.

Industry/Entity Type

Hotel

Contact Information for Business Card

Scott CurranReneson HotelsChief Operating Officer56 Madera DriveCorte Madera, CA 94925Office 415-891-5013Cell 707-5550143

```html
<!DOCTYPE html>
<html lang="en">
<head>
<meta charset="utf-8">
<title>Talvique Hotels Business Card</title>
<link rel="stylesheet" href="https://fonts.googleapis.com/css2?family=Montserrat:wght@400;500&family=Roboto:wght@500&display=swap">
<style>
  :root {
    --backdrop: #2b2b2b;
    --card-white: #ffffff;
    --navy: #0c3a61;
    --accent-green: #7cb342;
    --text-grey: #4f4f4f;
  }
  * { margin: 0; padding: 0; box-sizing: border-box; }
  html, body {
    width: 1200px; height: 900px; overflow: hidden;
    background: var(--backdrop);
  }
  .canvas { position: relative; width: 1200px; height: 900px; }
  .card {
    position: absolute; left: 261px; width: 656px; height: 358px;
    box-shadow: 0 4px 10px rgba(0,0,0,0.45);
  }
  .card-front { top: 69px; background: var(--card-white); }
  .card-back { top: 472px; background: var(--navy); }

  .brand-name {
    position: absolute;
    font-family: 'Montserrat', sans-serif;
    font-weight: 500;
    text-transform: uppercase;
    white-space: nowrap;
  }
  .card-front .brand-name {
    left: 33px; top: 164px;
    font-size: 25px; letter-spacing: 2.4px;
    color: var(--navy);
  }
  .card-back .brand-name {
    left: 0; right: 0; top: 150px; text-align: center;
    font-size: 40px; letter-spacing: 4px;
    color: var(--card-white);
  }

  .divider {
    position: absolute; left: 330px; top: 85px;
    width: 1.5px; height: 188px; background: var(--accent-green);
  }
  .contact-block {
    position: absolute; left: 359px; top: 80px;
    font-family: 'Montserrat', sans-serif; color: var(--text-grey);
  }
  .person-name {
    font-family: 'Roboto', sans-serif; font-weight: 500;
    font-size: 26px; line-height: 30px; color: var(--navy);
  }
  .person-title { font-size: 14px; letter-spacing: 0.9px; line-height: 18px; }
  .address { margin-top: 12px; font-size: 15.5px; letter-spacing: 1px; line-height: 22px; }
  .contact-list { list-style: none; margin-top: 10px; }
  .contact-list li {
    display: flex; align-items: center; height: 21.3px;
    font-size: 15.5px; letter-spacing: 0.9px;
  }
  .contact-list svg { width: 11px; height: 11px; margin-right: 8px; flex: none; }
</style>
</head>
<body>
<div class="canvas">
  <section class="card card-front">
    <div class="brand-name">Talvique Hotels</div>
    <div class="divider"></div>
    <div class="contact-block">
      <div class="person-name">Brent Holloway Talvique</div>
      <div class="person-title">Hotels Chief Operating Officer</div>
      <div class="address">83 Pellwick Lane<br>Larkmont, CA 94960</div>
      <ul class="contact-list">
        <li>
          <svg viewBox="0 0 12 12" aria-hidden="true"><path d="M2.5 1 L4.5 1 L5 3.5 L3.8 4.4 C4.5 6 6 7.5 7.6 8.2 L8.5 7 L11 7.5 L11 9.5 C11 10.5 10 11 9 11 C4.5 10.5 1.5 7.5 1 3 C1 2 1.5 1 2.5 1 Z" fill="none" stroke="#7cb342" stroke-width="1.2"/></svg>
          415-555-0186
        </li>
        <li>
          <svg viewBox="0 0 12 12" aria-hidden="true"><rect x="3" y="0.8" width="6.5" height="10.4" rx="1.2" fill="none" stroke="#7cb342" stroke-width="1.3"/><line x1="3" y1="8.6" x2="9.5" y2="8.6" stroke="#7cb342" stroke-width="1.2"/></svg>
          707-5550143
        </li>
        <li>
          <svg viewBox="0 0 12 12" aria-hidden="true"><rect x="0.8" y="2.5" width="10.4" height="7.5" rx="1" fill="none" stroke="#7cb342" stroke-width="1.2"/><path d="M1 3 L6 6.8 L11 3" fill="none" stroke="#7cb342" stroke-width="1.2"/></svg>
          info@talviquehotels.com
        </li>
        <li>
          <svg viewBox="0 0 12 12" aria-hidden="true"><circle cx="6" cy="6" r="5" fill="none" stroke="#7cb342" stroke-width="1.1"/><ellipse cx="6" cy="6" rx="2.2" ry="5" fill="none" stroke="#7cb342" stroke-width="1"/><line x1="1" y1="6" x2="11" y2="6" stroke="#7cb342" stroke-width="1"/><line x1="1.8" y1="3.5" x2="10.2" y2="3.5" stroke="#7cb342" stroke-width="0.9"/><line x1="1.8" y1="8.5" x2="10.2" y2="8.5" stroke="#7cb342" stroke-width="0.9"/></svg>
          www.talviquehotels.com
        </li>
      </ul>
    </div>
  </section>

  <section class="card card-back">
    <div class="brand-name">Talvique Hotels</div>
  </section>
</div>
</body>
</html>
```